Website redesign for Halt and Fullmane

We would like to update the design of our current website to a more concise, conversion optimized design.
The goal of our website is to get our message across as concisely as possible plus encourage people to contact us for more information or to book a consultation.
We need a redesign of the home page and 1 internal page - just for design/layout purposes/format purposes.

Target Market(s)

Males 20-45 years old who are concerned about hair loss and who want to regrow their own hair.

Industry/Entity Type

Health And Wellness

Number of Pages Required

2 page

Font styles to use
Sans Serif

Colors
00a990
33a6d7
ffffff
9d9d9d

Requirements
Must have
• We want the home page to be very concise and to the point in getting the message across. We want to get across the following 6 key messages:
• 1. Dr Pembrook story – why he created this solution
• 2. Hair loss is caused by a chemical imbalance
• 3. Halt and fullmane conducts genetic and DNA analysis, then rebalances body chemistry, thus reversing the hair loss process and enabling your own hair to regrow naturally
• 4. Money back guaranteed results
• 5. Purely Core ingredients – no harsh preservatives or chemicals are included
• 6. All ingredients are FDA approved and safe – no side effects
• We also need a strong call to action. We want people to call or email us to find out more information or to schedule a consultation.
• Here is our current website which is not performing as we would hope: http://www.haltandfullmane.example/
• Here is our press release for further information: https://www.pressdeskhub.example/news/finally-we-now-have-a-cure-for-male-pattern-baldness-28461902
• I uploaded the logo files, but let me know if anything else is needed and I can add it.

```html
<!DOCTYPE html>
<html lang="en">
<head>
<meta charset="utf-8">
<title>Halt &amp; Fullmane – Home</title>
<link rel="stylesheet" href="https://fonts.googleapis.com/css2?family=Jost:wght@300;400;500;600&family=Raleway:wght@400;700&display=swap">
<style>
:root{
  --teal:#00a990;
  --teal-dark:#00957f;
  --blue:#33a6d7;
  --white:#ffffff;
  --grey:#9d9d9d;
  --ink:#333333;
  --soft:#f0f0f0;
}
*{box-sizing:border-box;margin:0;padding:0}
html,body{width:1200px;height:2740px;overflow:hidden}
body{font-family:"Jost",sans-serif;color:var(--ink);background:var(--white);position:relative}
a{color:inherit;text-decoration:none}

/* Header */
.site-header{position:absolute;top:0;left:0;width:1200px;height:137px;background:var(--white)}
.brand{position:absolute;left:100px;top:34px;display:flex;align-items:center;gap:14px}
.brand-mark{width:56px;height:56px;background:var(--teal);border-radius:50%}
.brand-name{font-size:34px;font-weight:400;color:var(--teal);line-height:1}
.brand-sub{position:absolute;left:176px;top:80px;font-size:22px;color:var(--teal);font-weight:400}
.header-call{position:absolute;left:620px;top:56px;font-size:26px;color:var(--blue);display:flex;align-items:center;gap:10px}
.lang-select{position:absolute;left:948px;top:52px;width:154px;height:38px;border:1px solid #ddd;display:flex;align-items:center;padding:0 12px;gap:10px;font-size:12px;color:#777;letter-spacing:.5px}
.lang-flag{width:22px;height:13px;background:#2c4c9c}
.lang-select .caret{margin-left:auto;font-size:11px}

/* Navigation */
.main-nav{position:absolute;top:137px;left:0;width:1200px;height:55px;background:var(--teal)}
.main-nav ul{list-style:none;display:flex;margin-left:100px;height:55px}
.main-nav li{font-size:13px;color:var(--white);text-transform:uppercase;padding:0 18px;display:flex;align-items:center;letter-spacing:.3px}
.main-nav li.is-active{background:var(--teal-dark)}

/* Hero */
.hero{position:absolute;top:192px;left:0;width:1200px;height:590px;overflow:hidden}
.hero-photo{position:absolute;inset:0;background:linear-gradient(100deg,#c9c2bb 0%,#8d6c58 30%,#b8998a 55%,#6a4a3a 75%,#dcd5ce 100%)}
.hero-title{position:absolute;top:200px;left:0;width:1200px;text-align:center;color:var(--white);font-size:37px;font-weight:400;letter-spacing:4px;line-height:47px;text-transform:uppercase}
.hero-play{position:absolute;left:563px;top:295px}
.hero-arrow{position:absolute;top:232px}
.hero-arrow.prev{left:34px}
.hero-arrow.next{left:1136px}
.hero-curve{position:absolute;left:0;bottom:0}

/* Welcome */
.welcome{position:absolute;top:760px;left:0;width:1200px;height:503px;background:var(--blue);color:var(--white)}
.welcome h1{position:absolute;top:75px;width:1200px;text-align:center;font-size:31px;font-weight:400;letter-spacing:1px}
.welcome-intro{position:absolute;top:120px;left:150px;width:900px;text-align:center;font-size:11.5px;line-height:19px;font-weight:300}
.key-messages{position:absolute;top:180px;left:312px;width:640px;list-style:none}
.key-messages li{position:relative;padding-left:30px;font-size:15.5px;line-height:21px;margin-bottom:18px;font-weight:300}
.key-messages svg{position:absolute;left:0;top:2px}

/* Story */
.story{position:absolute;top:1263px;left:0;width:1200px;height:532px;background:var(--white)}
.story h2{position:absolute;top:93px;left:100px;width:590px;font-family:"Raleway",sans-serif;font-size:14.5px;font-weight:700;color:#666;line-height:24px}
.story-text{position:absolute;top:152px;left:100px;width:598px;font-size:10.5px;line-height:24px;color:var(--grey)}
.story-text p+p{margin-top:10px}
.story-visual{position:absolute;top:94px;left:728px;width:374px;height:355px;border:1px solid #ddd;padding:8px;background:var(--white)}
.story-visual div{width:100%;height:100%;background:linear-gradient(180deg,#e4efe0 0%,#7aa56a 55%,#5a4a3a 100%)}
.btn{display:inline-flex;align-items:center;justify-content:center;background:var(--teal);color:var(--white);font-size:16px;text-transform:uppercase;letter-spacing:.5px}
.story .btn{position:absolute;top:402px;left:100px;width:155px;height:44px}

/* Features */
.features{position:absolute;top:1795px;left:0;width:1200px;height:600px;background:var(--soft)}
.feature{position:absolute;top:80px;width:300px;text-align:center}
.feature-photo{width:240px;height:240px;margin:0 auto;border-radius:50%;border:4px solid var(--teal);padding:6px;background:var(--white)}
.feature-photo div{width:100%;height:100%;border-radius:50%}
.feature h3{margin-top:22px;font-size:15px;font-weight:500;text-transform:uppercase;color:#222}
.feature p{margin:14px auto 0;width:290px;font-size:11px;line-height:20px;color:#555;height:80px}
.feature .btn{margin-top:15px;width:152px;height:43px}

/* Footer */
.site-footer{position:absolute;top:2395px;left:0;width:1200px;height:345px;background:var(--teal);color:var(--white)}
.footer-col{position:absolute;top:50px}
.footer-col h4{font-size:17px;font-weight:400;text-transform:uppercase;letter-spacing:.3px;margin-bottom:18px}
.footer-col p{font-size:12.5px;line-height:30px;opacity:.85}
.contact-line{display:flex;align-items:center;gap:8px}
.newsletter{display:flex;margin-top:12px}
.newsletter input{width:218px;height:38px;border:0;padding:0 22px;font-family:inherit;font-size:11px;color:#aaa;letter-spacing:.5px}
.newsletter button{width:105px;height:38px;border:0;background:var(--teal-dark);color:var(--white);font-family:inherit;font-size:13px;text-transform:uppercase}
.social{display:flex;gap:12px;margin-top:14px}
.social span{width:36px;height:36px;border-radius:50%;background:var(--white)}
.footer-rule{position:absolute;top:272px;left:100px;width:1002px;height:1px;background:rgba(255,255,255,.4)}
.footer-legal{position:absolute;top:290px;left:100px;font-size:11.5px;opacity:.9}
</style>
</head>
<body>

<header class="site-header">
  <a class="brand" href="#">
    <span class="brand-mark"></span>
    <span class="brand-name">Halt &amp; Fullmane</span>
  </a>
  <span class="brand-sub">by Robert Pembrook M.D.</span>
  <a class="header-call" href="#">
    <svg width="22" height="22" viewBox="0 0 24 24"><path fill="#33a6d7" d="M6.6 10.8a15.1 15.1 0 0 0 6.6 6.6l2.2-2.2c.3-.3.7-.4 1-.2 1.1.4 2.3.6 3.6.6.6 0 1 .4 1 1V20c0 .6-.4 1-1 1A17 17 0 0 1 3 4c0-.6.4-1 1-1h3.5c.6 0 1 .4 1 1 0 1.3.2 2.5.6 3.6.1.3 0 .7-.2 1z"/></svg>
    Call Us: (555) 014-2290
  </a>
  <div class="lang-select"><span class="lang-flag"></span>ENGLISH<span class="caret">&#8964;</span></div>
</header>

<nav class="main-nav">
  <ul>
    <li class="is-active">Home</li>
    <li>About Us</li>
    <li>How It Works</li>
    <li>Success Stories</li>
    <li>FAQs</li>
    <li>Blog</li>
    <li>Salon Partners</li>
    <li>Book Now</li>
    <li>Contact</li>
  </ul>
</nav>

<section class="hero">
  <div class="hero-photo" role="img" aria-label="Woman holding a hairbrush with loose strands of hair, softly blurred"></div>
  <h2 class="hero-title">Stop hereditary hair loss and regrow a full<br>healthy head of hair</h2>
  <svg class="hero-play" width="74" height="74" viewBox="0 0 74 74"><circle cx="37" cy="37" r="34" fill="none" stroke="rgba(255,255,255,.6)" stroke-width="4"/><path d="M29 22 L52 37 L29 52 Z" fill="rgba(255,255,255,.6)"/></svg>
  <svg class="hero-arrow prev" width="20" height="36" viewBox="0 0 20 36"><path d="M17 2 L3 18 L17 34" fill="none" stroke="rgba(255,255,255,.7)" stroke-width="2"/></svg>
  <svg class="hero-arrow next" width="20" height="36" viewBox="0 0 20 36"><path d="M3 2 L17 18 L3 34" fill="none" stroke="rgba(255,255,255,.7)" stroke-width="2"/></svg>
  <svg class="hero-curve" width="1200" height="40" viewBox="0 0 1200 40" preserveAspectRatio="none"><path d="M0 22 Q300 0 600 18 T1200 10 L1200 40 L0 40 Z" fill="#33a6d7"/></svg>
</section>

<section class="welcome">
  <h1>WELCOME TO HALT &amp; FULLMANE</h1>
  <p class="welcome-intro">Dr. Robert Pembrook is a renowned hair restoration expert and was even a contributor in the development of the Advanced High Density MICROscopic single hair transplant procedure. As a practicing derma-surgeon, he also pioneered the non-surgical rhinoplasty and has a special interest in the field of developing non-surgical solutions.</p>
  <ul class="key-messages">
    <li><svg width="18" height="18" viewBox="0 0 18 18"><circle cx="9" cy="9" r="9" fill="#fff"/><path d="M5 9.3 L8 12 L13 6.5" fill="none" stroke="#33a6d7" stroke-width="2"/></svg>Dr Pembrook story – why he created this solution</li>
    <li><svg width="18" height="18" viewBox="0 0 18 18"><circle cx="9" cy="9" r="9" fill="#fff"/><path d="M5 9.3 L8 12 L13 6.5" fill="none" stroke="#33a6d7" stroke-width="2"/></svg>Hair loss is caused by a chemical imbalance</li>
    <li><svg width="18" height="18" viewBox="0 0 18 18"><circle cx="9" cy="9" r="9" fill="#fff"/><path d="M5 9.3 L8 12 L13 6.5" fill="none" stroke="#33a6d7" stroke-width="2"/></svg>Halt and fullmane conducts genetic and DNA analysis, then rebalances body chemistry, thus reversing the hair loss process and enabling your own hair to regrow naturally</li>
    <li><svg width="18" height="18" viewBox="0 0 18 18"><circle cx="9" cy="9" r="9" fill="#fff"/><path d="M5 9.3 L8 12 L13 6.5" fill="none" stroke="#33a6d7" stroke-width="2"/></svg>Money back guaranteed results</li>
    <li><svg width="18" height="18" viewBox="0 0 18 18"><circle cx="9" cy="9" r="9" fill="#fff"/><path d="M5 9.3 L8 12 L13 6.5" fill="none" stroke="#33a6d7" stroke-width="2"/></svg>Purely Core ingredients – no harsh preservatives or chemicals are included</li>
    <li><svg width="18" height="18" viewBox="0 0 18 18"><circle cx="9" cy="9" r="9" fill="#fff"/><path d="M5 9.3 L8 12 L13 6.5" fill="none" stroke="#33a6d7" stroke-width="2"/></svg>All ingredients are FDA approved and safe – no side effects</li>
  </ul>
</section>

<section class="story">
  <h2>The Revolutionary New Solution For Hair Loss That Uses Personalized Medicine To Stop Hair Loss and Regrow Your Thinning / Receding Hair.</h2>
  <div class="story-text">
    <p>Dr. Robert Pembrook, the creator of Halt and Fullmane is a renowned hair restoration expert. After seeing first his father and then older brothers thin and go bald, he dedicated his life to finding the cure for hair loss. After initially pioneering the single hair method for hair transplant, he determined there must be a non-surgical solution and spent the last 20 years in research and clinical trial and error first creating, then perfecting what is now the Halt and Fullmane solution for hair loss.</p>
    <p>To the right you can see the Pembrook family tree, or at least the five Pembrook brothers from oldest to youngest. Unluckily for the oldest three Dr Pembrook did not discover the cure until it was too late for them. As you can see both Robert and his younger brother (Robert is the second youngest) sport a full head of hair despite both now being well beyond the age when their older brothers had already lost their hair.</p>
  </div>
  <a class="btn" href="#">Read More</a>
  <div class="story-visual"><div role="img" aria-label="Family tree illustration with portraits of the five Pembrook brothers"></div></div>
</section>

<section class="features">
  <article class="feature" style="left:90px">
    <div class="feature-photo"><div role="img" aria-label="Stylist attending to a client's hair in a salon" style="background:linear-gradient(160deg,#d9d3cc,#6f8f86 60%,#3c3a38)"></div></div>
    <h3>Why is Halt and Fullmane unique?</h3>
    <p>Halt and Fullmane uses a scientific approach to hair loss by treating your unique cause. Every case is different and may include multiple causes. Unless we are treating yours, the treatment won't work for you.</p>
    <a class="btn" href="#">Read More</a>
  </article>
  <article class="feature" style="left:450px">
    <div class="feature-photo"><div role="img" aria-label="Young woman looking at a blister pack of pills" style="background:linear-gradient(160deg,#f1ece8,#c89a86 55%,#d8566a)"></div></div>
    <h3>Personalized Medicine</h3>
    <p>Halt and Fullmane uses FDA approved ingredients in a proprietary formula using individual dosages based on your personal biology and genetics. Our solution is formulated in our specialty compounding pharmacy.</p>
    <a class="btn" href="#">Read More</a>
  </article>
  <article class="feature" style="left:805px">
    <div class="feature-photo"><div role="img" aria-label="Tired man resting his head on a pillow" style="background:linear-gradient(160deg,#f4f2ee,#d3a987 55%,#9c6b4e)"></div></div>
    <h3>Holistic Approach</h3>
    <p>While many cases of hair loss are caused by a hormone imbalance (DHT), stress and diet can cause hair loss too. Your treatment will be multi-faceted to ensure your hair loss is stopped and we regrow your hair as quickly as possible.</p>
    <a class="btn" href="#">Read More</a>
  </article>
</section>

<footer class="site-footer">
  <div class="footer-col" style="left:100px">
    <h4>Hours of Operation</h4>
    <p>Monday - Friday: 9.00am to 5.00pm</p>
    <p>Saturday: 8.00am to 2.00pm</p>
  </div>
  <div class="footer-col" style="left:410px;width:310px">
    <h4>Contact Address</h4>
    <p>Halt and Fullmane Hair, LLC 4120 Larchmont Ave, Suite 300 Fairview CA 90000</p>
    <p class="contact-line"><svg width="13" height="13" viewBox="0 0 24 24"><path fill="#fff" d="M6.6 10.8a15.1 15.1 0 0 0 6.6 6.6l2.2-2.2c.3-.3.7-.4 1-.2 1.1.4 2.3.6 3.6.6.6 0 1 .4 1 1V20c0 .6-.4 1-1 1A17 17 0 0 1 3 4c0-.6.4-1 1-1h3.5c.6 0 1 .4 1 1 0 1.3.2 2.5.6 3.6.1.3 0 .7-.2 1z"/></svg>(555) 014-2290</p>
    <p class="contact-line"><svg width="13" height="11" viewBox="0 0 26 20"><rect width="26" height="20" rx="2" fill="#fff"/><path d="M1 2 L13 11 L25 2" fill="none" stroke="#00a990" stroke-width="2"/></svg>info@haltandfullmane.example</p>
  </div>
  <div class="footer-col" style="left:773px">
    <h4>Sign up for Newsletters</h4>
    <p style="font-size:11.5px;line-height:18px">Please sign up here for latest news</p>
    <form class="newsletter"><input type="text" value="EMAIL ADDRESS" readonly><button type="button">Subscribe</button></form>
    <div class="social"><span></span><span></span><span></span><span></span></div>
  </div>
  <div class="footer-rule"></div>
  <p class="footer-legal">© 2017 HALT &amp; FULLMANE SOLUTION. All right reserved . Term of Use</p>
</footer>

</body>
</html>
```